Just Sold Postcard

Real Estate/ Brindle Oak Realty.I'd like a template that I can use to change out the picture of the home, verbiage on the front, and address. I'm including a picture of what I've used in the past. I like designs that use red, with some blue and white. I'd like the ability to change the verbiage on the back as well.

Industry/Entity Type

Real Estate

Font styles to use
Serif
Sans Serif

```html
<!DOCTYPE html>
<html lang="en">
<head>
<meta charset="utf-8">
<title>Just Sold Postcard – Brindle Oak Realty</title>
<link rel="stylesheet" href="https://fonts.googleapis.com/css2?family=Josefin+Sans:wght@400;600&family=Archivo+Black&display=swap">
<style>
  :root {
    --backdrop: #5b5d5c;
    --card-white: #ffffff;
    --card-paper: #f4f4f4;
    --brand-red: #ec2227;
    --brand-navy: #2b2d7a;
    --text-white: #ffffff;
  }
  * { box-sizing: border-box; margin: 0; padding: 0; }
  html, body { width: 1200px; height: 1000px; overflow: hidden; }
  body {
    background: var(--backdrop);
    position: relative;
    font-family: "Josefin Sans", sans-serif;
  }

  /* ---------- Mailing side ---------- */
  .postcard-back {
    position: absolute; left: 197px; top: 111px;
    width: 578px; height: 436px;
    background: var(--card-white);
  }
  .agent-panel {
    position: absolute; left: 33px; top: 36px;
    width: 229px; height: 323px;
    background: var(--brand-red);
    color: var(--text-white);
    text-align: center;
  }
  .agent-panel__name { font-size: 30px; font-weight: 400; margin-top: 30px; letter-spacing: 0.5px; }
  .agent-panel__address { font-size: 13px; line-height: 16px; margin-top: 6px; letter-spacing: 0.3px; }
  .agent-panel__offer { font-size: 14px; line-height: 20px; margin-top: 10px; letter-spacing: 0.6px; font-weight: 600; }
  .contact-badge {
    width: 104px; height: 104px; border-radius: 50%;
    background: var(--brand-navy);
    border: 4px solid var(--text-white);
    margin: 14px auto 0;
    display: flex; align-items: center; justify-content: center;
    font-family: "Archivo Black", sans-serif;
    font-size: 15px; line-height: 21px; color: var(--text-white);
  }
  .agent-panel__contact { font-size: 13px; line-height: 21px; margin-top: 16px; letter-spacing: 0.3px; }
  .stamp-box {
    position: absolute; left: 451px; top: 36px;
    width: 95px; height: 92px;
    border: 2px solid var(--brand-navy);
  }
  .address-lines { position: absolute; left: 310px; top: 215px; width: 235px; }
  .address-lines span { display: block; height: 3px; background: var(--brand-navy); margin-bottom: 25px; }

  /* ---------- Front side ---------- */
  .postcard-front {
    position: absolute; left: 454px; top: 449px;
    width: 577px; height: 436px;
    background: var(--card-paper);
  }
  .front-header {
    position: absolute; left: 0; top: 68px; width: 100%;
    display: flex; align-items: center; justify-content: center; gap: 22px;
  }
  .front-header__agent { color: var(--brand-red); font-size: 37px; letter-spacing: 1.5px; }
  .brokerage-name {
    display: flex; align-items: center; gap: 8px;
    color: var(--brand-navy); font-size: 27px; font-weight: 600;
  }
  .brokerage-name__mark { width: 14px; height: 14px; border-radius: 50%; background: var(--brand-navy); }
  .home-photo {
    position: absolute; left: 0; top: 144px; width: 100%; height: 173px;
    background: linear-gradient(90deg, #1f2f47 0%, #3b5a73 35%, #6b7a62 60%, #3e5a2e 100%);
  }
  .feature-badge {
    position: absolute; left: 218px; top: 157px;
    width: 148px; height: 148px; border-radius: 50%;
    background: rgba(245,245,245,0.95);
    border: 4px solid var(--brand-red);
    display: flex; align-items: center; justify-content: center;
    text-align: center; color: var(--brand-navy);
    font-size: 14px; line-height: 20px; padding-top: 4px;
  }
  .just-sold {
    position: absolute; left: 0; top: 340px; width: 100%;
    text-align: center; color: var(--brand-red);
    font-family: "Archivo Black", sans-serif;
    font-size: 54px; letter-spacing: 5px;
  }
</style>
</head>
<body>
  <section class="postcard-back">
    <div class="agent-panel">
      <h1 class="agent-panel__name">Dana Whitfield</h1>
      <p class="agent-panel__address">Your address, street, name<br>country etc</p>
      <p class="agent-panel__offer">For a free Market<br>Analysis of your home</p>
      <div class="contact-badge">Contact<br>me<br>today</div>
      <p class="agent-panel__contact">Call: (555)-204-3187<br>Email: whitfield.dana@brindlemail.com</p>
    </div>
    <div class="stamp-box"></div>
    <div class="address-lines"><span></span><span></span><span></span></div>
  </section>

  <section class="postcard-front">
    <header class="front-header">
      <span class="front-header__agent">Dana Whitfield</span>
      <span class="brokerage-name"><span class="brokerage-name__mark"></span>Brindle Oak Realty</span>
    </header>
    <div class="home-photo" role="img" aria-label="Photo of the sold home: villa with pool at dusk and garden driveway"></div>
    <div class="feature-badge">Fabulous<br>End Unit<br>with granite<br>countertop and<br>hardwood<br>floors</div>
    <div class="just-sold">JUST SOLD!</div>
  </section>
</body>
</html>
```